Design Website Templates for Photographers for Lumera Inc. (trylumera.example)

Lumera Inc. is a generative website company for wedding photographers.
We are seeking new photography website design inspirations for the next template to be offered on our platform. The catch is you must use the same data for your designs. You also must use all of the data somewhere in the design. You cannot add new content besides the data available. If you wish to add any elements It will be hardcoded and must be universally fitting for many different photographers. We recommend not using any hardcoded test.
Don't be afraid to be creative! Although the most important element of a photographers website is the photos, we are looking for unique and out-of-the-box designs for the actual site as well.
Here is the User generated data available to you:
- 4 Hero Images Landscape, 4 Hero Images Portrait
- Tagline “destination photographer based in Maui, Hawaii”
- “About Photo” of the photographer
- “About” Biography Text
- The design can use up to 3 colors + background color and 2 fonts
- 9 Gallery images
- 3 Packages/services that include landscape/portrait images, a price, a title and text
- Testimonials made up of an image, text and text for the name of testimonial giver
See some examples of our current website designs attached. You can use any of the data you see in the designs.
Updates
We are looking for designs that are less feminine and are more neutral in color and fonts. Currently our templates are more oriented towards feminine photographers. We want to have designs that speak to diverse audiences. We thank everyone for submitting and are reviewing the designs.
Number of Pages Required
1 page
Look and feel
Each slider illustrates characteristics of the customer's brand and the style your logo design should communicate.

```html
<!DOCTYPE html>
<html lang="en">
<head>
<meta charset="utf-8">
<title>Lumera — Destination Photographer</title>
<link href="https://fonts.googleapis.com/css2?family=Lora:wght@400;500&family=Raleway:wght@400;500;600&display=swap" rel="stylesheet">
<style>
:root{
  --ink:#1a1a1a;
  --text:#5a5a5a;
  --paper:#efeeeb;
  --white:#ffffff;
  --black:#000000;
  --footer:#2b2b2b;
  --accent:#f5b90a;
}
*{box-sizing:border-box;margin:0;padding:0}
html,body{width:1200px;height:5208px;overflow:hidden}
body{position:relative;background:var(--paper);font-family:'Lora',serif;color:var(--ink)}
.abs{position:absolute}
.photo{position:absolute}
.serif-title{font-family:'Lora',serif;font-weight:400;font-size:38px;letter-spacing:1px;text-align:center;position:absolute;left:0;width:1200px}
.body-copy{font-family:'Lora',serif;font-size:13.5px;line-height:25.8px;color:var(--text);text-align:justify}
.btn-outline{position:absolute;border:1.5px solid #444;font-family:'Raleway',sans-serif;font-size:12px;font-weight:500;letter-spacing:.5px;color:#222;display:flex;align-items:center;justify-content:center}

/* hero */
.hero{position:absolute;left:0;top:0;width:1200px;height:689px;overflow:hidden;background:#6e5a45}
.hero-photo{left:0;top:0;width:1200px;height:689px;
  background:linear-gradient(90deg,#a58a5e 0%,#c9ad7e 18%,#e7d3bf 34%,#d9b9a2 46%,#4f4a4c 62%,#383a40 78%,#6a5d4a 100%)}
.nav{position:absolute;left:0;top:0;width:1200px;height:85px;background:rgba(0,0,0,.32)}
.logo{position:absolute;left:110px;top:18px;font-family:'Raleway',sans-serif;font-weight:500;font-size:40px;letter-spacing:3px;color:var(--white)}
.nav-link{position:absolute;top:32px;font-family:'Raleway',sans-serif;font-size:12px;color:var(--white);letter-spacing:.3px}
.nav-active{position:absolute;left:402px;top:82px;width:38px;height:3px;background:var(--white)}
.nav-cta{position:absolute;left:933px;top:20px;width:154px;height:40px;border:1.5px solid var(--white);color:var(--white);font-family:'Raleway',sans-serif;font-size:12px;display:flex;align-items:center;justify-content:center}
.tagline{position:absolute;left:0;top:354px;width:1200px;text-align:center;font-family:'Lora',serif;font-weight:400;font-size:38px;line-height:46px;color:var(--white);text-shadow:0 1px 6px rgba(0,0,0,.35)}
.thumb{position:absolute;border:2px solid rgba(255,255,255,.8)}

/* about */
.about-title{top:782px}
.about-copy{position:absolute;left:139px;top:846px;width:436px}
.about-photo{left:630px;top:854px;width:432px;height:332px;background:radial-gradient(ellipse at 55% 50%,#e6ddd2 0%,#8e7a66 22%,#3a2e26 50%,#15110e 100%)}

/* biography */
.bio-band{position:absolute;left:0;top:1309px;width:1200px;height:131px;background:var(--black)}
.bio-band h2{position:absolute;left:0;top:43px;width:1200px;text-align:center;font-weight:400;font-size:38px;color:var(--white)}
.bio-area{position:absolute;left:0;top:1440px;width:1200px;height:703px;background:var(--white)}
.frame{position:absolute;border:1.5px solid #222}
.bio-couple{left:218px;top:1600px;width:290px;height:180px;background:radial-gradient(ellipse at 55% 45%,#6d5a4c 0%,#b9a898 35%,#ece7e2 70%,#ffffff 100%)}
.bio-portrait{left:164px;top:1677px;width:266px;height:266px;border-radius:50%;border:6px solid var(--white);box-shadow:0 0 0 3px #333;background:radial-gradient(circle at 50% 55%,#8a6e52 0%,#a99a8a 35%,#a8a8a8 60%,#8e8e8e 100%)}
.bio-copy{position:absolute;left:563px;top:1592px;width:435px}

/* gallery */
.g{position:absolute}

/* packages */
.pkg-title{top:3307px}
.pkg{position:absolute;top:3388px;width:305px;text-align:center}
.pkg-photo{width:305px;height:357px}
.pkg h3{font-weight:400;font-size:21px;line-height:35px;margin-top:24px;color:#222}
.pkg p{font-size:12px;line-height:22px;color:#333;margin-top:6px}
.pkg a{display:inline-block;margin-top:8px;font-size:13px;color:#222;text-decoration:underline}

/* testimonials */
.testi{position:absolute;left:0;top:4004px;width:1200px;height:578px;background:linear-gradient(180deg,#3a3936 0%,#24231f 40%,#1a1917 70%,#121110 100%)}
.testi-title{top:4092px;color:var(--white)}
.quote-copy{position:absolute;width:408px;font-size:13.5px;line-height:25.8px;color:var(--white);text-align:justify}
.quote-name{position:absolute;font-size:20px;color:var(--white)}
.quote-co{position:absolute;font-size:12px;color:var(--white)}

/* contact */
.connect-title{top:4676px}
.field{position:absolute;border:2px solid #555;border-radius:4px;font-family:'Raleway',sans-serif;font-size:13px;color:#777;padding-left:20px;display:flex;align-items:center}
.field.area{align-items:flex-start;padding-top:16px}
.submit{position:absolute;left:483px;top:4949px;width:242px;height:47px;background:var(--accent);font-family:'Raleway',sans-serif;font-weight:600;font-size:13px;display:flex;align-items:center;justify-content:center;color:#111}

/* footer */
.footer{position:absolute;left:0;top:5103px;width:1200px;height:105px;background:var(--footer)}
.footer p{position:absolute;left:0;top:42px;width:1200px;text-align:center;font-family:'Raleway',sans-serif;font-size:12.5px;color:var(--white)}
</style>
</head>
<body>

<header class="hero">
  <div class="photo hero-photo" role="img" aria-label="Hero photograph of a smiling couple embracing in a sunlit meadow"></div>
  <nav class="nav">
    <div class="logo">LUMERA</div>
    <span class="nav-link" style="left:402px">HOME</span>
    <span class="nav-link" style="left:466px">ABOUT</span>
    <span class="nav-link" style="left:534px">BLOG</span>
    <span class="nav-link" style="left:594px">TESTIMONIALS</span>
    <span class="nav-link" style="left:711px">PORTFOLIO</span>
    <span class="nav-link" style="left:808px">GET IN TOUCH</span>
    <div class="nav-active"></div>
    <div class="nav-cta">BOOK WITH ME</div>
  </nav>
  <h1 class="tagline">Destination Photographer<br>Based in Maui, Hawaii</h1>
  <div class="thumb" role="img" aria-label="Hero slide thumbnail of a couple" style="left:380px;top:588px;width:80px;height:54px;background:linear-gradient(90deg,#c9a878,#e2d2c0 50%,#44403e)"></div>
  <div class="thumb" role="img" aria-label="Active hero slide thumbnail of a couple" style="left:486px;top:576px;width:122px;height:80px;border:3px solid #fff;background:linear-gradient(90deg,#d6c2a4,#ede4da 50%,#3c3a3c)"></div>
  <div class="thumb" role="img" aria-label="Hero slide thumbnail of a couple outdoors" style="left:636px;top:588px;width:80px;height:54px;background:linear-gradient(90deg,#e6e2dc,#f4f1ec 50%,#4a4a50)"></div>
  <div class="thumb" role="img" aria-label="Hero slide thumbnail of a couple by the sea" style="left:739px;top:588px;width:80px;height:54px;background:linear-gradient(90deg,#cdd6e0,#f0f0f2 50%,#2e3440)"></div>
</header>

<section>
  <h2 class="serif-title about-title">ABOUT PHOTO</h2>
  <p class="body-copy about-copy">Lorem ipsum dolor sit amet, consectetur adipiscing elit, sed do eiusmod tempor incididunt ut labore et dolore magna aliqua. Ut enim ad minim veniam, quis nostrud exercitation ullamco laboris nisi ut aliquip ex ea commodo consequat. Duis aute irure dolor in reprehenderit in voluptate velit esse cillum dolore eu fugiat nulla pariatur. Excepteur sint occaecat cupidatat non proident, sunt in culpa qui officia deserunt mollit anim id est laborum. Lorem ipsum dolor sit amet, consectetur adipiscing elit, sed do eiusmod tempor incididunt ut labore et dolore magna aliqua. Ut enim ad minim veniam, quis nostrud exercitation ullamco laboris nisi ut aliquip ex ea commodo consequat.</p>
  <div class="btn-outline" style="left:139px;top:1145px;width:154px;height:40px">LEARN MORE</div>
  <div class="photo about-photo" role="img" aria-label="Photograph of a couple dancing under falling sparkles at night"></div>
</section>

<section>
  <div class="bio-band"><h2>OUR BIOGRAPHY</h2></div>
  <div class="bio-area"></div>
  <div class="frame" style="left:111px;top:1511px;width:960px;height:507px"></div>
  <div class="frame" style="left:129px;top:1529px;width:960px;height:505px"></div>
  <div class="photo bio-couple" role="img" aria-label="Faded photograph of a couple kissing"></div>
  <div class="photo bio-portrait" role="img" aria-label="Round portrait of the photographer"></div>
  <p class="body-copy bio-copy">Lorem ipsum dolor sit amet, consectetur adipiscing elit, sed do eiusmod tempor incididunt ut labore et dolore magna aliqua. Ut enim ad minim veniam, quis nostrud exercitation ullamco laboris nisi ut aliquip ex ea commodo consequat. Duis aute irure dolor in reprehenderit in voluptate velit esse cillum dolore eu fugiat nulla pariatur. Excepteur sint occaecat cupidatat non proident, sunt in culpa qui officia deserunt mollit anim id est laborum. Lorem ipsum dolor sit amet, consectetur adipiscing elit, sed do eiusmod tempor incididunt ut labore et dolore magna aliqua. Ut enim ad minim veniam, quis nostrud exercitation ullamco laboris nisi ut aliquip ex ea commodo consequat.</p>
  <div class="btn-outline" style="left:563px;top:1893px;width:154px;height:37px">LEARN MORE</div>
</section>

<section class="gallery">
  <div class="g" role="img" aria-label="Gallery photo: couple walking on a beach at sunset" style="left:8px;top:2143px;width:382px;height:263px;background:linear-gradient(180deg,#4e5a7a 0%,#9a8ea0 30%,#f0b27a 48%,#d9a58a 62%,#b88a72 100%)"></div>
  <div class="g" role="img" aria-label="Gallery photo: couple touching foreheads, bride with flower crown" style="left:410px;top:2143px;width:380px;height:519px;background:linear-gradient(90deg,#b98c6a 0%,#e8c8a8 30%,#c89478 50%,#3a3533 75%,#1e1d1f 100%)"></div>
  <div class="g" role="img" aria-label="Gallery photo: couple silhouetted holding hands at sunset" style="left:810px;top:2143px;width:382px;height:263px;background:linear-gradient(180deg,#2c2e38 0%,#5a4a48 40%,#e09a52 62%,#5a3a28 80%,#1e1714 100%)"></div>
  <div class="g" role="img" aria-label="Gallery photo: groom kissing bride's forehead among greenery" style="left:8px;top:2426px;width:382px;height:501px;background:linear-gradient(90deg,#233022 0%,#4a3a2e 30%,#7a5e4c 50%,#c9a890 70%,#eeeae6 100%)"></div>
  <div class="g" role="img" aria-label="Gallery photo: couple walking under confetti" style="left:410px;top:2693px;width:380px;height:519px;background:linear-gradient(90deg,#5e6a3e 0%,#d6c8ae 30%,#ece4da 55%,#f4eee8 75%,#8a8a60 100%)"></div>
  <div class="g" role="img" aria-label="Gallery photo: groom spinning bride in a golden field" style="left:810px;top:2426px;width:382px;height:501px;background:linear-gradient(180deg,#ece6dc 0%,#ddd2c2 45%,#d8ccc4 62%,#9a7e58 78%,#6a5236 100%)"></div>
  <div class="g" role="img" aria-label="Gallery photo: couple with sparklers at night" style="left:8px;top:2947px;width:382px;height:265px;background:radial-gradient(circle at 35% 35%,#f0c070 0%,#a86a2c 25%,#4a2e1c 55%,#120d0a 100%)"></div>
  <div class="g" role="img" aria-label="Gallery photo: couple embracing with white bouquet" style="left:810px;top:2947px;width:382px;height:265px;background:linear-gradient(90deg,#8c8074 0%,#f2efe8 25%,#2c2f3c 50%,#d8b8a4 70%,#f4f2ee 100%)"></div>
</section>

<section>
  <h2 class="serif-title pkg-title">FEATURED PACKAGES</h2>
  <div class="pkg" style="left:111px">
    <div class="pkg-photo" role="img" aria-label="Package photo: couple walking through a meadow" style="background:linear-gradient(180deg,#9ea690 0%,#7a8268 35%,#5a5e52 55%,#c8c2b8 75%,#6e7256 100%)"></div>
    <h3>Wedding Collection<br>One</h3>
    <p>Lorem ipsum dolor sit amet, consectetur<br>adipiscing elit, sed do eiusmod</p>
    <a>More Info</a>
  </div>
  <div class="pkg" style="left:446px">
    <div class="pkg-photo" role="img" aria-label="Package photo: couple kissing at golden hour" style="background:linear-gradient(90deg,#e8d0a0 0%,#f2ece2 35%,#c8a888 55%,#2a2a2e 75%,#6a5a44 100%)"></div>
    <h3>Wedding Collection<br>Two</h3>
    <p>Lorem ipsum dolor sit amet, consectetur<br>adipiscing elit, sed do eiusmod</p>
    <a>More Info</a>
  </div>
  <div class="pkg" style="left:784px">
    <div class="pkg-photo" role="img" aria-label="Package photo: couple by a white brick wall" style="background:linear-gradient(90deg,#e8e6e2 0%,#4a4038 30%,#2e2c2a 45%,#f0ece6 65%,#8a9a78 85%,#d8d4cc 100%)"></div>
    <h3>Wedding Collection<br>Three</h3>
    <p>Lorem ipsum dolor sit amet, consectetur<br>adipiscing elit, sed do eiusmod</p>
    <a>More Info</a>
  </div>
</section>

<section>
  <div class="testi" role="img" aria-label="Dark background photograph of a couple in the mountains"></div>
  <h2 class="serif-title testi-title">TESTIMONIALS</h2>
  <svg class="abs" style="left:0;top:4160px" width="1200" height="330" viewBox="0 0 1200 330" fill="none" stroke="#ffffff" stroke-width="2">
    <path d="M112 10 H580 V274 H214 L210 318 L166 274 H112 Z"/>
    <path d="M619 10 H1087 V274 H720 L716 318 L672 274 H619 Z"/>
  </svg>
  <p class="quote-copy" style="left:141px;top:4190px">Lorem ipsum dolor sit amet, consectetur adipiscing elit, sed do eiusmod tempor incididunt ut labore et dolore magna aliqua. Ut enim ad minim veniam, quis nostrud exercitation ullamco laboris nisi ut aliquip ex ea commodo consequat. Duis aute irure dolor in reprehenderit in voluptate velit esse cillum dolore eu fugiat nulla pariatur.</p>
  <span class="quote-name" style="left:141px;top:4370px">John doe</span>
  <span class="quote-co" style="left:253px;top:4378px">Company name</span>
  <p class="quote-copy" style="left:648px;top:4190px">Lorem ipsum dolor sit amet, consectetur adipiscing elit, sed do eiusmod tempor incididunt ut labore et dolore magna aliqua. Ut enim ad minim veniam, quis nostrud exercitation ullamco laboris nisi ut aliquip ex ea commodo consequat. Duis aute irure dolor in reprehenderit in voluptate velit esse cillum dolore eu fugiat nulla pariatur.</p>
  <span class="quote-name" style="left:648px;top:4370px">John doe</span>
  <span class="quote-co" style="left:760px;top:4378px">Company name</span>
</section>

<section>
  <h2 class="serif-title connect-title">LETS CONNECT</h2>
  <div class="field" style="left:220px;top:4749px;width:247px;height:51px">Name</div>
  <div class="field" style="left:481px;top:4749px;width:247px;height:51px">Email</div>
  <div class="field" style="left:741px;top:4749px;width:247px;height:51px">Phone</div>
  <div class="field area" style="left:220px;top:4818px;width:768px;height:118px">Text here..</div>
  <div class="submit">SUBMIT NOW</div>
</section>

<footer class="footer">
  <p>© Copyrights 2023 The Company Name | All Rights Reserved</p>
</footer>

</body>
</html>
```